Need a redesign for our Wordpress Credit report website

Hi, We need someone to redesign our Wordpress credit report website, lumenledger.co.za. The designer will be responsible for the following pages:
- home page
- blog page
- single post
- dashboard
- credit report page

About LumenLedger.co.za
Lumen Ledger is a consumer focussed credit report platform where South African citizens can get an easy to understand credit report that shows them where to improve their credit scores.

```html
<!DOCTYPE html>
<html lang="en">
<head>
<meta charset="utf-8">
<title>Lumen Ledger – Check your credit score</title>
<link href="https://fonts.googleapis.com/css2?family=Rubik:ital,wght@0,300;0,400;0,500;0,700;1,300;1,400&display=swap" rel="stylesheet">
<style>
:root{
  --blue:#1f5fb4;
  --blue-deep:#1a4f9a;
  --green:#8dc63f;
  --ink:#111418;
  --text:#555b63;
  --muted:#8a9096;
  --navy:#10305e;
  --line:#c9ced4;
  --white:#ffffff;
  --star:#f2b01e;
}
*{box-sizing:border-box;margin:0;padding:0}
html,body{width:1200px;height:4000px;overflow:hidden;background:var(--white)}
body{position:relative;font-family:"Rubik",sans-serif;color:var(--text)}
.abs{position:absolute}
.green{color:var(--green)}
.dots{position:absolute;display:flex;gap:5px;transform:translateX(-50%)}
.dots i{width:9px;height:9px;border-radius:50%;background:var(--blue);display:block}
.dots i+i{background:var(--green)}
.dots.on-green i+i,.dots.on-grad i+i{background:var(--white)}
.section-title{position:absolute;left:0;width:1200px;text-align:center;font-weight:700;font-size:40px;line-height:50px;color:var(--ink);text-transform:uppercase;white-space:nowrap}
.btn{position:absolute;display:flex;align-items:center;justify-content:center;background:var(--blue);color:var(--white);font-weight:500;font-size:16px;border-radius:30px;text-transform:uppercase;letter-spacing:.3px}

/* header */
.brand{left:144px;top:14px;display:flex;align-items:center;gap:10px}
.brand-mark{width:62px;height:62px;border-radius:50%;background:var(--green)}
.brand-name{font-size:27px;font-weight:400;color:var(--blue)}
.nav{left:554px;top:36px;display:flex;gap:40px;font-size:16px;font-weight:500;color:var(--ink)}
.nav .active{border-left:3px solid var(--green);padding-left:8px}
.login{left:950px;top:25px;width:105px;height:45px;font-size:17px}

/* hero */
.hero-title{left:144px;top:174px;width:420px;font-size:38px;line-height:53px;font-weight:700;color:var(--ink);text-transform:uppercase;white-space:nowrap}
.hero-list{left:144px;top:355px;list-style:none;font-size:18px;font-weight:300;color:#3d4349}
.hero-list li{display:flex;align-items:center;gap:19px;height:37.5px}
.hero-list li::before{content:"";width:19px;height:19px;border-radius:50%;background:linear-gradient(135deg,var(--green) 45%,var(--blue) 55%)}
.hero-cta{left:144px;top:535px;width:202px;height:58px}
.side-dots{left:52px;top:361px}
.side-dots i{display:block;width:8px;height:8px;border-radius:50%;background:#c8c8c8;margin-bottom:16px}
.side-dots i.on{background:var(--blue)}
.mouse{left:590px;top:562px}
.hero-art{left:596px;top:145px;width:600px;height:560px}

/* why */
.feature-title{position:absolute;font-size:17px;font-weight:500;line-height:28px;color:var(--ink)}
.feature-text{position:absolute;font-size:14px;line-height:24px;font-weight:300;color:var(--text)}
.read-more{position:absolute;font-size:18px;font-weight:500;color:var(--green);text-transform:uppercase}
.right{text-align:right}
.just{text-align:justify}

/* system features */
.features-photo{left:0;top:1561px;width:600px;height:499px;background:linear-gradient(135deg,#2b3f55,#3f5f7a 45%,#1d2e40)}
.features-panel{left:600px;top:1561px;width:600px;height:499px;background:var(--green)}
.features-title{left:674px;top:1672px;font-size:39px;line-height:48px;font-weight:700;color:var(--white);white-space:nowrap}
.features-list{left:674px;top:1742px;list-style:none;color:var(--white);font-size:16px;font-weight:500}
.features-list li{height:35.2px;display:flex;align-items:center;gap:26px}
.features-list li::before{content:"";width:13px;height:13px;border-radius:50%;background:var(--white)}

/* testimonials */
.testimonial-bg{left:0;top:2060px;width:1200px;height:622px;background:linear-gradient(90deg,#f3f4f5 0%,#eceae8 55%,#e4e2e0 75%,#f1f2f3 100%)}
.avatar{left:556px;top:2284px;width:88px;height:88px;border-radius:50%;border:3px solid var(--blue);background:linear-gradient(180deg,#cfd8e2,#9fb2c6)}
.quote{left:200px;width:800px;top:2392px;text-align:center;font-style:italic;font-weight:300;font-size:19px;line-height:31px;color:#6a6f75}
.reviewer{left:0;width:1200px;top:2514px;text-align:center;font-size:18px;font-weight:500;color:var(--blue)}
.stars{color:var(--star);letter-spacing:1px;margin-left:8px;font-size:22px}
.circle-arrow{position:absolute;width:40px;height:40px;border-radius:50%;border:1.5px solid #555;display:flex;align-items:center;justify-content:center}

/* reviews */
.reviews{left:0;top:2682px;width:1200px;height:518px;background:linear-gradient(100deg,var(--blue-deep) 0%,#2f6fb0 35%,#6ea35a 70%,var(--green) 100%)}
.review{position:absolute;width:330px;text-align:center;color:var(--white)}
.review .rstars{font-size:26px;letter-spacing:2px;line-height:30px}
.review p{font-style:italic;font-weight:300;font-size:17px;line-height:28px;margin-top:14px}
.review h4{font-size:17px;font-weight:500;margin-top:20px}

/* get started */
.start-bg{left:0;top:3200px;width:1200px;height:522px;background:linear-gradient(180deg,#f7f8f9,#eef0f2 60%,#e6e8ea)}
.field{position:absolute;height:53px;border:2px solid var(--line);background:var(--white);font-size:15px;color:#4a5056;display:flex;align-items:center;padding-left:20px}
.start-cta{left:498px;top:3579px;width:202px;height:57px}

/* footer */
.footer{left:0;top:3722px;width:1200px;height:278px;background:var(--navy);color:var(--white)}
.foot-col{position:absolute;top:57px}
.foot-col h3{font-size:20px;font-weight:500;text-transform:uppercase;margin-bottom:13px}
.foot-col a{display:block;color:var(--white);text-decoration:none;font-size:12px;line-height:24px;text-transform:uppercase}
.social{position:absolute;width:22px;height:22px;border-radius:50%;background:var(--white)}
.copy{position:absolute;left:163px;top:233px;font-size:12px}
.card{position:absolute;top:232px;width:37px;height:20px;background:var(--white);border-radius:2px}
</style>
</head>
<body>

<header>
  <div class="abs brand"><span class="brand-mark"></span><span class="brand-name">Lumen Ledger</span></div>
  <nav class="abs nav"><span class="active">HOME</span><span>ARTICLES</span><span>ABOUT</span><span>CONTACT</span></nav>
  <div class="btn login">LOGIN</div>
</header>

<section class="hero">
  <h1 class="abs hero-title">Check your credit<br><span class="green">score within</span><br>seconds</h1>
  <ul class="abs hero-list">
    <li>See your most recent credit score</li>
    <li>Get access to your full credit profile</li>
    <li>See who has been looking at your profile</li>
    <li>See if you have any adverse or Blacklistings</li>
  </ul>
  <div class="btn hero-cta">Get started now</div>
  <div class="abs side-dots"><i></i><i class="on"></i><i></i></div>
  <svg class="abs mouse" width="20" height="40" viewBox="0 0 20 40" aria-label="Scroll down">
    <rect x="2" y="1" width="16" height="26" rx="8" fill="none" stroke="#111418" stroke-width="1.6"/>
    <line x1="10" y1="6" x2="10" y2="11" stroke="#111418" stroke-width="1.6"/>
    <path d="M6 30l4 4 4-4M6 34l4 4 4-4" fill="none" stroke="#111418" stroke-width="1.4"/>
  </svg>
  <svg class="abs hero-art" viewBox="0 0 600 560">
    <circle cx="118" cy="126" r="124" fill="#1f5fb4"/>
    <circle cx="428" cy="274" r="172" fill="#8dc63f"/>
    <rect x="78" y="158" width="470" height="400" rx="14" fill="#d9dde2" role="img" aria-label="Computer and tablet screens showing a sample credit report with a score gauge"/>
  </svg>
</section>

<section class="why">
  <div class="dots" style="left:600px;top:784px"><i></i><i></i></div>
  <h2 class="section-title" style="top:814px">Why get your <span class="green">score from us?</span></h2>

  <h3 class="feature-title" style="left:144px;top:964px;width:280px">We don't abuse your<br>personal information</h3>
  <p class="feature-text just" style="left:144px;top:1036px;width:274px">Companies that give out free credit scores use your personal information to sell you financial products. That's how they can afford to give it to you for free. We believe that your personal information should be protected and not abused.</p>
  <div class="read-more" style="left:144px;top:1196px">Read more</div>

  <h3 class="feature-title" style="left:712px;top:964px;width:280px">Our report is super easy to<br>understand</h3>
  <p class="feature-text just" style="left:712px;top:1036px;width:298px">Our credit report is one of the easiest reports to understand. The report is clearly laid out and you will see immediately if you can apply for finance, if you are blacklisted, and where you can improve.</p>
  <div class="read-more" style="left:712px;top:1172px">Read more</div>

  <h3 class="feature-title right" style="left:200px;top:1262px;width:303px">300,000 + South<br>Africans have trusted us</h3>
  <p class="feature-text right" style="left:165px;top:1334px;width:342px">Since 2008 we have helped over 300,000 South Africans make sense of their credit reports, so you can rest assured knowing that we have a proven track record and that you are in safe hands with us.</p>
  <div class="read-more" style="left:407px;top:1452px">Read more</div>

  <svg class="abs" style="left:430px;top:960px" width="640" height="520" viewBox="0 0 640 520">
    <g stroke="#1f5fb4" stroke-width="4" fill="none">
      <line x1="153" y1="210" x2="170" y2="314"/>
      <line x1="300" y1="368" x2="424" y2="324"/>
    </g>
    <circle cx="422" cy="324" r="7" fill="#8dc63f"/>
    <circle cx="116" cy="109" r="96" fill="#fff" stroke="#1f5fb4" stroke-width="7"/>
    <circle cx="116" cy="109" r="82" fill="#8dc63f"/>
    <circle cx="116" cy="78" r="26" fill="#fff"/>
    <path d="M62 150 q0-42 54-42 q30 0 44 14 l-10 28 z" fill="#fff"/>
    <circle cx="146" cy="136" r="25" fill="#fff"/>
    <circle cx="146" cy="124" r="4" fill="#8dc63f"/>
    <rect x="142" y="131" width="8" height="20" fill="#8dc63f"/>
    <circle cx="526" cy="314" r="96" fill="#fff" stroke="#1f5fb4" stroke-width="7"/>
    <g fill="#8dc63f">
      <rect x="482" y="332" width="14" height="34"/><rect x="502" y="316" width="14" height="50"/>
      <rect x="522" y="324" width="14" height="42"/><rect x="542" y="298" width="14" height="68"/>
      <rect x="474" y="366" width="100" height="4"/>
    </g>
    <polyline points="484,310 506,292 528,302 558,276" fill="none" stroke="#8dc63f" stroke-width="5"/>
    <circle cx="211" cy="409" r="96" fill="#fff" stroke="#1f5fb4" stroke-width="7"/>
    <g fill="#8dc63f">
      <circle cx="211" cy="384" r="22"/><path d="M175 448 q0-44 36-44 q36 0 36 44 z"/>
      <circle cx="166" cy="396" r="14"/><path d="M140 436 q0-28 26-28 q16 0 22 10 l-8 18 z"/>
      <circle cx="256" cy="396" r="14"/><path d="M282 436 q0-28 -26-28 q-16 0 -22 10 l8 18 z"/>
    </g>
  </svg>
</section>

<section class="system">
  <div class="abs features-photo" role="img" aria-label="Photo of hands typing on a laptop displaying a credit score gauge"></div>
  <div class="abs features-panel"></div>
  <div class="dots on-green" style="left:688px;top:1644px"><i></i><i></i></div>
  <h2 class="abs features-title">SYSTEM FEATURES</h2>
  <ul class="abs features-list">
    <li>Dispute generator - easily manage disputes</li>
    <li>Budget tool - easily create a budget</li>
    <li>Improve your credit score eBook</li>
    <li>Personal Budgeting Spreadsheet</li>
    <li>Perfect score video course</li>
    <li>Personal Finance Video Tutorials</li>
    <li>Dedicated 24/7 Support</li>
  </ul>
</section>

<section class="testimonials">
  <div class="abs testimonial-bg" role="img" aria-label="Soft faded photo of a smiling woman reading"></div>
  <div class="dots" style="left:600px;top:2166px"><i></i><i></i></div>
  <h2 class="section-title" style="top:2196px">User <span class="green">testimonials</span></h2>
  <div class="abs avatar" role="img" aria-label="Customer portrait"></div>
  <p class="abs quote">The report was accurate and gave me a good understanding of my current credit status. I found it interesting the way the scoring worked and really enjoyed reading it...guess because I am doing well with managing credit.</p>
  <div class="abs reviewer">-Carla Vermeulen <span class="stars">★★★★★</span></div>
  <div class="circle-arrow" style="left:551px;top:2586px"><svg width="14" height="14" viewBox="0 0 14 14"><path d="M9 2 4 7l5 5" stroke="#444" stroke-width="1.8" fill="none"/></svg></div>
  <div class="circle-arrow" style="left:607px;top:2586px"><svg width="14" height="14" viewBox="0 0 14 14"><path d="M5 2l5 5-5 5" stroke="#444" stroke-width="1.8" fill="none"/></svg></div>
</section>

<section class="reviews-section">
  <div class="abs reviews"></div>
  <div class="dots on-grad" style="left:600px;top:2766px"><i></i><i></i></div>
  <h2 class="section-title" style="top:2798px;color:var(--white);width:1140px">Trusted reviews</h2>
  <div class="review" style="left:198px;top:2918px">
    <div class="rstars">★★★★★</div>
    <p>Their customer support team has been very impressive. The tools and knowledge they shared were of great practical use.</p>
    <h4>Nadia Steyn</h4>
  </div>
  <div class="review" style="left:642px;top:2918px">
    <div class="rstars">★★★★★</div>
    <p>Excellent credit report service. They respond to queries promptly, and have a very detailed credit report which is helpful and informative</p>
    <h4>Ironline Fitness ZA</h4>
  </div>
  <svg class="abs" style="left:92px;top:2986px" width="34" height="68" viewBox="0 0 34 68"><path d="M32 2 2 34l30 32" stroke="#fff" stroke-width="2" fill="none"/></svg>
  <svg class="abs" style="left:1074px;top:2986px" width="34" height="68" viewBox="0 0 34 68"><path d="M2 2l30 32-30 32" stroke="#fff" stroke-width="2" fill="none"/></svg>
</section>

<section class="start">
  <div class="abs start-bg" role="img" aria-label="Faded photo of a desk with a keyboard and notepad"></div>
  <div class="dots" style="left:600px;top:3289px"><i></i><i></i></div>
  <h2 class="section-title" style="top:3318px">Get <span class="green">started</span> now</h2>
  <div class="field" style="left:143px;top:3418px;width:298px">ID Number</div>
  <div class="field" style="left:450px;top:3418px;width:298px">First Name</div>
  <div class="field" style="left:757px;top:3418px;width:300px">Last Name</div>
  <div class="field" style="left:143px;top:3481px;width:452px">Primary Email</div>
  <div class="field" style="left:605px;top:3481px;width:452px">Mobile Number</div>
  <div class="btn start-cta">Get started now</div>
</section>

<footer class="abs footer">
  <div class="foot-col" style="left:163px"><h3>Terms</h3><a>General terms of use</a><a>Exclusion of liability</a><a>Security policy</a><a>Privacy policy</a></div>
  <div class="foot-col" style="left:425px"><h3>Purchase</h3><a>Delivery policy</a><a>Data policy</a><a>Refund policy</a><a>Charges and fees</a></div>
  <div class="foot-col" style="left:663px"><h3>Quick links</h3><a>About us</a><a>Articles</a><a>Contact us</a><a>Login</a></div>
  <div class="foot-col" style="left:905px"><h3>Social media</h3></div>
  <span class="social" style="left:907px;top:97px"></span>
  <span class="social" style="left:954px;top:97px"></span>
  <span class="social" style="left:907px;top:138px"></span>
  <span class="social" style="left:954px;top:138px"></span>
  <p class="copy">© 2022 All Rights Reserved LumenLedger.co.za I NCR Reg. No. NCRCB00</p>
  <span class="card" style="left:861px"></span>
  <span class="card" style="left:907px"></span>
  <span class="card" style="left:953px"></span>
  <span class="card" style="left:1000px"></span>
</footer>

</body>
</html>
```